Create a business promotion flyer to leave in customer mailboxes. We are a bulk petroleum supplier, servicing any industry that requires diesel. Base in griffith NSW, servicing griffith area and surrounds.

Business Name - Terra Diesel
Fuel@terradiesel-example.com.au
Owen - 0491 570 362 ohartley@terradiesel-example.com.au
Liam - 0491 570 718 lprosser@terradiesel-example.com.au
Simon - 0491 570 905 skenway@terradiesel-example.com.au
Office 02 5550 1734

Bulk Fuel deliveries.
Oils & lubricants
Local Family owned business

```html
<!DOCTYPE html>
<html lang="en">
<head>
<meta charset="utf-8">
<title>Terra Diesel – Flyer</title>
<link rel="stylesheet" href="https://fonts.googleapis.com/css2?family=Poppins:wght@400;500;600;700;800&display=swap">
<style>
  :root {
    --backdrop: #cbcbcb;
    --paper: #ffffff;
    --red: #e8282a;
    --charcoal: #3a3a3c;
    --ink: #3b3b3d;
    --sky-pale: #e9eff6;
    --sky: #8fb0d4;
    --sky-deep: #6f95c2;
    --steel: #aeb6bf;
    --steel-dark: #8b9299;
    --yard: #cfcdc8;
  }
  * { box-sizing: border-box; margin: 0; padding: 0; }
  html, body { width: 980px; height: 1200px; overflow: hidden; background: var(--backdrop); }
  body { font-family: "Poppins", sans-serif; position: relative; }

  .flyer {
    position: absolute; left: 154px; top: 125px;
    width: 671px; height: 949px;
    background: var(--paper); overflow: hidden;
  }

  .hero-photo {
    position: absolute; left: 0; top: 0; width: 671px; height: 540px;
    background: linear-gradient(180deg,
      #ffffff 0%, #ffffff 20%,
      var(--sky-pale) 30%, var(--sky) 44%, var(--sky-deep) 54%,
      var(--steel) 56%, #c3c9cf 64%, var(--steel-dark) 74%, #9ea3a7 80%,
      var(--yard) 82%, var(--yard) 100%);
  }

  .brand {
    position: absolute; left: 0; right: 0; top: 104px;
    display: flex; align-items: center; justify-content: center; gap: 14px;
  }
  .brand-mark {
    width: 40px; height: 40px; border-radius: 50%; background: var(--red);
  }
  .brand-name {
    font-weight: 600; font-size: 56px; line-height: 1;
    color: var(--red); letter-spacing: -0.5px;
  }

  .hero-curve { position: absolute; left: 0; top: 430px; width: 671px; height: 361px; }

  .services { position: absolute; left: 0; top: 574px; width: 671px; height: 160px; }
  .service { position: absolute; top: 0; width: 230px; text-align: center; color: #fff; }
  .service .badge {
    width: 90px; height: 90px; margin: 0 auto; border-radius: 50%;
    background: #fff; border: 2px solid var(--red);
    display: flex; align-items: center; justify-content: center;
  }
  .service .label { margin-top: 14px; font-weight: 500; font-size: 24px; line-height: 23px; }
  .service--bulk { left: 7px; }
  .service--oils { left: 189px; }
  .service--local { left: 386px; }

  .enquiries {
    position: absolute; left: 63px; top: 762px; width: 549px; height: 51px;
    background: var(--red); border-radius: 26px;
    color: #fff; font-weight: 500; font-size: 18px;
    display: flex; align-items: center; justify-content: center;
  }

  .contacts {
    position: absolute; left: 10px; right: 10px; top: 829px;
    display: grid; grid-template-columns: repeat(3, 1fr); text-align: center;
  }
  .contact-name { color: var(--red); font-weight: 800; font-size: 14.5px; line-height: 18px; }
  .contact-email { color: var(--ink); font-size: 11px; line-height: 18px; letter-spacing: -0.2px; white-space: nowrap; }

  .divider {
    position: absolute; left: 46px; right: 40px; top: 879px; height: 1px;
    background: linear-gradient(90deg, transparent, #f2b1a5 20%, #f2b1a5 80%, transparent);
  }

  .office {
    position: absolute; left: 0; right: 0; top: 891px;
    display: flex; align-items: center; justify-content: center; gap: 14px;
    font-weight: 700; font-size: 35px; line-height: 40px; color: var(--ink);
  }
  .office .number { color: var(--red); }
</style>
</head>
<body>
  <main class="flyer">
    <div class="hero-photo" role="img" aria-label="Photo of a white road-train fuel tanker with two trailers parked in front of a large steel warehouse under a cloudy blue sky"></div>

    <header class="brand">
      <span class="brand-mark" aria-hidden="true"></span>
      <h1 class="brand-name">Terra Diesel</h1>
    </header>

    <svg class="hero-curve" viewBox="0 0 671 361" preserveAspectRatio="none" aria-hidden="true">
      <path d="M0 15 Q335 165 671 15 L671 361 L0 361 Z" fill="var(--red)"/>
      <path d="M0 45 Q335 175 671 15 L671 361 L0 361 Z" fill="var(--charcoal)"/>
    </svg>

    <section class="services">
      <div class="service service--bulk">
        <div class="badge">
          <svg width="64" height="40" viewBox="0 0 64 40" fill="none" stroke="var(--red)" stroke-width="2" stroke-linejoin="round">
            <rect x="3" y="6" width="40" height="16" rx="8"/>
            <path d="M44 10 H52 L60 20 V30 H44 Z"/>
            <path d="M48 13 H52 L56 19 H48 Z"/>
            <path d="M2 26 H60 V30 H2 Z"/>
            <circle cx="11" cy="33" r="4"/><circle cx="21" cy="33" r="4"/><circle cx="51" cy="33" r="4"/>
          </svg>
        </div>
        <p class="label">Bulk Fuel<br>deliveries</p>
      </div>
      <div class="service service--oils">
        <div class="badge">
          <svg width="56" height="52" viewBox="0 0 56 52" fill="none" stroke="var(--red)" stroke-width="2" stroke-linejoin="round">
            <path d="M4 20 H16 V46 H4 Z"/><path d="M7 20 V15 H13 V20"/>
            <rect x="7" y="28" width="6" height="10"/>
            <ellipse cx="30" cy="8" rx="10" ry="4"/>
            <path d="M20 8 V44 A10 4 0 0 0 40 44 V8"/>
            <path d="M20 20 A10 4 0 0 0 40 20"/><path d="M20 32 A10 4 0 0 0 40 32"/>
            <path d="M46 26 C50 32 52 35 52 38 A6 6 0 0 1 40 38 C40 35 42 32 46 26 Z" fill="#fff"/>
          </svg>
        </div>
        <p class="label">Oils &amp;<br>lubricants</p>
      </div>
      <div class="service service--local">
        <div class="badge">
          <svg width="54" height="48" viewBox="0 0 54 48" fill="none" stroke="var(--red)" stroke-width="2" stroke-linejoin="round">
            <path d="M4 22 L27 4 L50 22"/>
            <path d="M10 18 V44 H44 V18"/>
            <path d="M22 44 V30 H32 V44"/>
            <path d="M38 8 V13"/>
          </svg>
        </div>
        <p class="label">Local Family<br>owned business</p>
      </div>
    </section>

    <p class="enquiries">General Enquiries: Fuel@terradiesel-example.com.au</p>

    <section class="contacts">
      <div class="contact">
        <p class="contact-name">Owen - 0491 570 362</p>
        <p class="contact-email">ohartley@terradiesel-example.com.au</p>
      </div>
      <div class="contact">
        <p class="contact-name">Liam - 0491 570 718</p>
        <p class="contact-email">lprosser@terradiesel-example.com.au</p>
      </div>
      <div class="contact">
        <p class="contact-name">Simon - 0491 570 905</p>
        <p class="contact-email">skenway@terradiesel-example.com.au</p>
      </div>
    </section>

    <div class="divider"></div>

    <p class="office">
      <svg width="42" height="32" viewBox="0 0 42 32" aria-hidden="true">
        <path d="M3 12 C3 4 39 4 39 12 L39 15 L30 15 L30 10 C26 8 16 8 12 10 L12 15 L3 15 Z" fill="var(--red)"/>
        <path d="M13 14 H29 L36 29 H6 Z" fill="var(--red)"/>
        <circle cx="21" cy="21" r="5" fill="#fff"/><circle cx="21" cy="21" r="2.5" fill="var(--red)"/>
      </svg>
      <span>Office <span class="number">02 5550 1734</span></span>
    </p>
  </main>
</body>
</html>
```